Law Offices business card

Hi there, I'll need business card for the Law Offices of Colin Matheny. The information must convey his strategic approach and quick resolution to complex business litigation needs. Please emphasize Civil Litigation, Corporate Law, Business Governance and Real Estate Law. Colin has over 25 years of experience in these fields.The card should be modern and edgy and the message should be clear. Please consult his current website for ideas.

```html
<!DOCTYPE html>
<html lang="en">
<head>
<meta charset="utf-8">
<title>Law Offices of Colin Matheny – Business Card</title>
<link rel="stylesheet" href="https://fonts.googleapis.com/css2?family=Open+Sans:wght@400;600&display=swap">
<style>
  :root {
    --orange: #fb6000;
    --charcoal: #4a4a4a;
    --ink: #1c1c1c;
    --paper: #ffffff;
    --backdrop: #e8e5e2;
  }
  * { margin: 0; padding: 0; box-sizing: border-box; }
  html, body { width: 1200px; height: 900px; overflow: hidden; }
  body {
    background: var(--backdrop);
    font-family: "Open Sans", Arial, sans-serif;
    position: relative;
  }
  .card {
    position: absolute;
    background: var(--paper);
    box-shadow: 0 6px 18px rgba(0,0,0,0.18);
    overflow: hidden;
  }
  .card--front { left: 78px; top: 34px; width: 588px; height: 364px; }
  .card--back  { left: 388px; top: 505px; width: 567px; height: 352px; }

  .card__bands { position: absolute; left: 0; top: 0; }

  .brand { position: absolute; display: flex; align-items: center; gap: 34px; }
  .brand__dot {
    flex: none;
    width: 96px; height: 96px; border-radius: 50%;
    background: var(--orange);
  }
  .brand__name {
    color: var(--orange);
    font-weight: 600;
    font-size: 25px;
    line-height: 1.25;
    text-transform: uppercase;
    white-space: nowrap;
  }
  .card--front .brand { left: 107px; top: 51px; }
  .card--back .brand  { left: 105px; top: 125px; }

  .holder { position: absolute; left: 50px; top: 223px; color: var(--paper); }
  .holder__name { font-size: 20px; font-weight: 600; line-height: 1.2; }
  .holder__role { font-size: 15px; line-height: 1.3; }
  .holder__address { margin-top: 22px; font-size: 15px; line-height: 21px; }

  .contacts {
    position: absolute; right: 36px; top: 230px;
    list-style: none; color: var(--paper);
    font-size: 14.5px; text-align: right;
  }
  .contacts li { display: flex; justify-content: flex-end; align-items: center; gap: 8px; height: 24.5px; }
  .contacts svg { width: 12px; height: 12px; fill: var(--paper); }

  .services {
    position: absolute; left: 0; right: 0; top: 256px;
    text-align: center; color: var(--ink);
    font-size: 16px; font-weight: 600; line-height: 30px;
  }
  .services .sep { margin: 0 10px; }
</style>
</head>
<body>

  <section class="card card--front" aria-label="Business card front">
    <svg class="card__bands" width="588" height="364" viewBox="0 0 588 364" aria-hidden="true">
      <polygon points="0,179 387,179 372,206 0,206" fill="var(--charcoal)"/>
      <polygon points="412,171 588,171 588,364 0,364 0,206 381,206" fill="var(--orange)"/>
    </svg>

    <div class="brand">
      <span class="brand__dot" aria-hidden="true"></span>
      <span class="brand__name">Law Offices<br>of Colin Matheny</span>
    </div>

    <div class="holder">
      <p class="holder__name">Colin Matheny</p>
      <p class="holder__role">Attorney</p>
      <p class="holder__address">118B Harbor Lane<br>Coral Bay, Florida 33012</p>
    </div>

    <ul class="contacts">
      <li>555-310-4827
        <svg viewBox="0 0 24 24"><path d="M6.6 10.8a15 15 0 0 0 6.6 6.6l2.2-2.2c.3-.3.7-.4 1-.2 1.1.4 2.3.6 3.6.6.6 0 1 .4 1 1V20c0 .6-.4 1-1 1A17 17 0 0 1 3 4c0-.6.4-1 1-1h3.5c.6 0 1 .4 1 1 0 1.3.2 2.5.6 3.6.1.3 0 .7-.2 1z"/></svg>
      </li>
      <li>555-310-4890
        <svg viewBox="0 0 24 24"><path d="M6 2h10v6H6zM3 9h18v13H3zm3 3v2h3v-2zm5 0v2h3v-2zm5 0v2h3v-2zM6 16v2h3v-2zm5 0v2h3v-2z"/></svg>
      </li>
      <li>colin@mathenylaw.com
        <svg viewBox="0 0 24 24"><path d="M2 5h20v14H2zm2 2v.5l8 5 8-5V7z"/></svg>
      </li>
      <li>www.mathenylaw.com
        <svg viewBox="0 0 24 24"><path d="M12 2a10 10 0 1 0 0 20 10 10 0 0 0 0-20zm-1 3v3H8l1-2zm2 0 2 1 1 2h-3zM5 11h3v2H5zm5 0h4v2h-4zm6 0h3v2h-3zm-8 5h3v3l-2-1zm5 0h3l-1 2-2 1z"/></svg>
      </li>
    </ul>
  </section>

  <section class="card card--back" aria-label="Business card back">
    <div class="brand">
      <span class="brand__dot" aria-hidden="true"></span>
      <span class="brand__name">Law Offices<br>of Colin Matheny</span>
    </div>
    <p class="services">
      Civil Litigation<span class="sep">|</span>Corporate Law<br>
      Business Governance<span class="sep">|</span>Real Estate Law
    </p>
  </section>

</body>
</html>
```